Coastline Premier Retreats Business Card Design

Design a business card for Coastline Premier Retreats. Look at the website for colors and reference. Card should have logo, name, title, office number, mobile number, email, URL and a tagline like, "Luxury Hotel & Resort Email Marketing" (This might change).

https://www.coastlinepremierretreats.example

The rest I will leave up to your imagination.

Contact Information for Business Card

Logo, name, title, office number, mobile number, email, URL and a tagline like, "Luxury Hotel & Resort Email Marketing" (This might change).

```html
<!DOCTYPE html>
<html lang="en">
<head>
<meta charset="utf-8">
<title>Coastline Premier Retreats – Business Card</title>
<link rel="stylesheet" href="https://fonts.googleapis.com/css2?family=Open+Sans:wght@400;600;700;800&display=swap">
<style>
  :root {
    --stage: #232323;
    --card-dark: #1f1f23;
    --card-dark-shade: #19191c;
    --brand-orange: #f47521;
    --text-light: #ffffff;
    --text-muted: #e6e6e6;
  }
  * { box-sizing: border-box; margin: 0; padding: 0; }
  html, body {
    width: 1200px; height: 780px; overflow: hidden;
    background: var(--stage);
    font-family: "Open Sans", Arial, sans-serif;
  }
  .stage {
    position: relative; width: 1200px; height: 780px;
    display: flex; align-items: center; justify-content: center; gap: 40px;
  }
  .card {
    position: relative; width: 540px; height: 309px; overflow: hidden;
    box-shadow: 0 18px 40px rgba(0,0,0,.45);
  }
  /* Front side */
  .card--front { background: var(--card-dark); }
  .card__shade {
    position: absolute; inset: 0; width: 100%; height: 100%;
  }
  .brand-name {
    font-weight: 800; text-transform: uppercase; letter-spacing: .02em;
    line-height: 1.05;
  }
  .card--front .brand-name {
    position: absolute; left: 30px; top: 28px;
    font-size: 22px; color: var(--text-light);
  }
  .contact-block {
    position: absolute; right: 28px; bottom: 22px;
    text-align: right; color: var(--text-light);
  }
  .person-name { font-size: 27px; font-weight: 700; line-height: 1.1; }
  .person-name__first { color: var(--brand-orange); }
  .person-role { font-size: 13px; margin-top: 2px; }
  .tagline {
    font-size: 12.5px; color: var(--brand-orange); line-height: 1.35; margin-top: 4px;
  }
  .contact-list { list-style: none; margin-top: 8px; font-size: 12.5px; line-height: 1.5; color: var(--text-muted); }
  .contact-list li { display: flex; align-items: center; justify-content: flex-end; gap: 8px; }
  .contact-icon { width: 12px; height: 12px; flex: none; }
  /* Back side */
  .card--back {
    background: var(--brand-orange);
    display: flex; align-items: center; justify-content: center;
  }
  .card--back .brand-name { font-size: 34px; color: var(--text-light); text-align: center; }
</style>
</head>
<body>
<main class="stage">
  <article class="card card--front" aria-label="Business card front">
    <svg class="card__shade" viewBox="0 0 540 309" preserveAspectRatio="none" aria-hidden="true">
      <polygon points="0,118 540,190 540,309 0,309" fill="var(--card-dark-shade)"/>
    </svg>
    <p class="brand-name">Coastline<br>Premier Retreats</p>
    <div class="contact-block">
      <h1 class="person-name"><span class="person-name__first">Lena</span> Marwick</h1>
      <p class="person-role">Co-Founder</p>
      <p class="tagline">Luxury Hotel &amp;<br>Resort Email Marketing</p>
      <ul class="contact-list">
        <li>(555) 014-2758
          <svg class="contact-icon" viewBox="0 0 24 24" aria-hidden="true"><path fill="var(--brand-orange)" d="M6.6 10.8a15.1 15.1 0 0 0 6.6 6.6l2.2-2.2a1 1 0 0 1 1-.25 11.4 11.4 0 0 0 3.6.57 1 1 0 0 1 1 1V20a1 1 0 0 1-1 1A17 17 0 0 1 3 4a1 1 0 0 1 1-1h3.5a1 1 0 0 1 1 1c0 1.25.2 2.45.57 3.57a1 1 0 0 1-.25 1z"/></svg>
        </li>
        <li>(555) 018-7777
          <svg class="contact-icon" viewBox="0 0 24 24" aria-hidden="true"><rect x="6" y="2" width="12" height="20" rx="2" fill="none" stroke="var(--brand-orange)" stroke-width="2"/><circle cx="12" cy="18" r="1.2" fill="var(--brand-orange)"/></svg>
        </li>
        <li>www.coastlinepremierretreats.example
          <svg class="contact-icon" viewBox="0 0 24 24" aria-hidden="true"><circle cx="12" cy="12" r="9" fill="none" stroke="var(--brand-orange)" stroke-width="2"/><path d="M3 12h18M12 3c3 3 3 15 0 18M12 3c-3 3-3 15 0 18" fill="none" stroke="var(--brand-orange)" stroke-width="1.6"/></svg>
        </li>
        <li>info@coastlinepremierretreats.example
          <svg class="contact-icon" viewBox="0 0 24 24" aria-hidden="true"><rect x="3" y="5" width="18" height="14" rx="1.5" fill="var(--brand-orange)"/><path d="M3.5 6l8.5 7 8.5-7" fill="none" stroke="var(--card-dark)" stroke-width="1.8"/></svg>
        </li>
      </ul>
    </div>
  </article>

  <article class="card card--back" aria-label="Business card back">
    <p class="brand-name">Coastline<br>Premier Retreats</p>
  </article>
</main>
</body>
</html>
```